BRISKEL Need a luxury modern business card designed.

Need a luxury modern business card designed. refer to the uploaded files for the company name and logo in the zip file under source files. i will making my descion on monday. so please send in before then so if we need to edit we will have the time. we have a trade show coming up and im on a deadline for printer.

Target Market(s)

high end clients

Contact Information for Business Card

Company nAme and logo. Tobias Fennick Co-Founder / Project Manager Office # 555-318-7094 Cell # 555-642-1586 BRISKEL.CA Tobias@briskel-example.ca

Font styles to use
Other font styles liked:
• Modern

Requirements
Must have
• Company name and logo, contact info, using the black, gold and white color scheme.

```html
<!DOCTYPE html>
<html lang="en">
<head>
<meta charset="utf-8">
<title>BRISKEL Business Card</title>
<link href="https://fonts.googleapis.com/css2?family=Roboto:wght@400;500;700&display=swap" rel="stylesheet">
<style>
  :root {
    --backdrop: #3b322d;
    --card: #242424;
    --card-back: #1c1c1c;
    --white: #f2f2f2;
    --gold: #a8925a;
    --emboss-dark: #141414;
    --emboss-light: #2c2c2c;
  }
  * { margin: 0; padding: 0; box-sizing: border-box; }
  html, body {
    width: 1200px; height: 847px; overflow: hidden;
    background: var(--backdrop);
    font-family: "Roboto", Arial, sans-serif;
  }
  .stage {
    position: relative; width: 1200px; height: 847px;
    display: flex; align-items: center; justify-content: center; gap: 50px;
  }
  .card {
    position: relative; width: 540px; height: 309px;
    border-radius: 4px;
    box-shadow: 0 12px 30px rgba(0,0,0,0.45);
    overflow: hidden;
  }
  .card--back { background: var(--card-back); }
  .card--front { background: var(--card); }

  .brand {
    position: absolute; display: flex; align-items: center; gap: 12px;
    font-weight: 400; letter-spacing: 8px; font-size: 34px;
  }
  .brand__square { width: 14px; height: 14px; }

  .card--back .brand {
    left: 50%; top: 50%; transform: translate(-50%, -50%);
    color: var(--emboss-dark);
    text-shadow: 1px 1px 0 var(--emboss-light);
  }
  .card--back .brand__square { background: var(--emboss-dark); box-shadow: 1px 1px 0 var(--emboss-light); }

  .card--front .brand { left: 70px; top: 62px; color: var(--white); }
  .card--front .brand__square { background: var(--gold); }

  .rule {
    position: absolute; left: 60px; right: 40px; top: 190px;
    height: 1px; background: var(--gold);
  }
  .person {
    position: absolute; right: 44px; top: 138px; text-align: right;
  }
  .person__name {
    color: var(--gold); font-weight: 700; font-size: 19px; text-transform: uppercase;
    letter-spacing: 0.3px;
  }
  .person__title { color: var(--white); font-size: 14px; margin-top: 2px; }

  .contacts {
    position: absolute; left: 60px; top: 206px; list-style: none;
    color: var(--white); font-size: 15px; line-height: 20px;
  }
  .contacts li { display: flex; align-items: center; gap: 8px; }
  .contacts svg { width: 12px; height: 12px; fill: var(--gold); flex: none; }
</style>
</head>
<body>
<main class="stage">
  <section class="card card--back" aria-label="Card back">
    <div class="brand"><span class="brand__square"></span>BRISKEL</div>
  </section>

  <section class="card card--front" aria-label="Card front">
    <div class="brand"><span class="brand__square"></span>BRISKEL</div>
    <div class="person">
      <div class="person__name">Tobias Fennick</div>
      <div class="person__title">Co-Founder / Project Manager</div>
    </div>
    <div class="rule"></div>
    <ul class="contacts">
      <li>
        <svg viewBox="0 0 12 12"><path d="M2.5 0.8 4.3 3 3.4 4.3C4 5.8 6.2 8 7.7 8.6L9 7.7l2.2 1.8-1.2 1.8C6 11 1 6 0.7 2z"/></svg>
        555-318-7094
      </li>
      <li>
        <svg viewBox="0 0 12 12"><path d="M3 0h6v12H3zM4 1.5v8h4v-8z"/></svg>
        555-642-1586
      </li>
      <li>
        <svg viewBox="0 0 12 12"><path d="M0 2h12v8H0zM1 3l5 3.5L11 3z"/></svg>
        Tobias@briskel-example.ca
      </li>
      <li>
        <svg viewBox="0 0 12 12"><circle cx="6" cy="6" r="5.5"/></svg>
        BRISKEL.CA
      </li>
    </ul>
  </section>
</main>
</body>
</html>
```